Dynamic Business Card for Sports Supplements Company

Hi! I'm looking for an awesome business card to match my existing sports supplement company. I have uploaded my current company logo and screenshot of the front page of my website.

I would like to have something dynamic and interesting and utilize the colors in the website - the reds and purples

The business card should be double sided and focus on a unique eye-catching design on the back and include all the relevant company info.

Most importantly, it should say somewhere: "Sign up on our website for a coupon code."

Target Market(s)

Mostly for women gym goers but it shouldn't be too feminine. It should be in keeping with the website design. It should flow and clearly be connected to it

Industry/Entity Type

Business

Contact Information for Business Card

Lorraine K. Vestal
CEO
LVestal@Quorvanexco.com
www.quorvanexco.com
555.417.3820
P.O. Box 47315
Fernhollow, Calder 00000

Sign up on our website for a coupon code

Font styles to use
Serif
Sans Serif
Other font styles liked:
• Novecento font family and "Quorvanex" is in AR Destine font

Requirements
Must have
• One side should be a bold Quorvanex logo design. Even just the symbol itself may be o.k. (see attached file)

```html
<!DOCTYPE html>
<html lang="en">
<head>
<meta charset="utf-8">
<title>Quorvanex Business Card</title>
<link rel="stylesheet" href="https://fonts.googleapis.com/css2?family=Open+Sans:wght@400;600;700&display=swap">
<style>
  :root {
    --ink: #0b0b0b;
    --red: #e31e24;
    --red-deep: #b5121b;
    --paper: #ffffff;
    --text: #3a3a3a;
    --backdrop: #e6e3de;
  }
  * { box-sizing: border-box; margin: 0; padding: 0; }
  html, body { width: 1200px; height: 950px; overflow: hidden; }
  body {
    background: var(--backdrop);
    font-family: "Open Sans", Arial, sans-serif;
    position: relative;
  }
  .card {
    position: absolute;
    top: 125px;
    width: 400px;
    height: 700px;
    overflow: hidden;
    box-shadow: 0 10px 30px rgba(0,0,0,0.25);
  }
  .card-front { left: 150px; background: var(--paper); }
  .card-back { left: 650px; background: var(--red); }

  .front-header { position: absolute; inset: 0; width: 400px; height: 420px; }

  .brand-front {
    position: absolute;
    top: 175px; left: 0; width: 400px;
    text-align: center;
    color: var(--paper);
    font-weight: 700;
    font-size: 40px;
    letter-spacing: 3px;
  }

  .contact {
    position: absolute;
    top: 440px; left: 0; width: 400px;
    text-align: center;
    color: var(--text);
  }
  .contact-name {
    color: var(--red);
    font-weight: 600;
    font-size: 22px;
    letter-spacing: 1.5px;
    text-transform: uppercase;
  }
  .contact-title { font-size: 17px; margin-bottom: 14px; }
  .contact-address { font-size: 17px; line-height: 1.35; margin-bottom: 10px; }
  .contact-lines { list-style: none; font-size: 17px; line-height: 1.6; }
  .contact-lines li { display: flex; align-items: center; justify-content: center; gap: 8px; }
  .contact-lines svg { width: 16px; height: 16px; flex: none; }

  .brand-back {
    position: absolute;
    top: 310px; left: 0; width: 400px;
    display: flex; align-items: center; justify-content: center; gap: 14px;
    color: var(--paper);
    font-weight: 700;
    font-size: 44px;
    letter-spacing: 3px;
  }
  .brand-back .mark { width: 30px; height: 30px; background: var(--paper); }

  .coupon-note {
    position: absolute;
    bottom: 70px; left: 0; width: 400px;
    text-align: center;
    color: var(--paper);
    font-size: 16px;
    font-weight: 600;
  }
</style>
</head>
<body>

<section class="card card-front" aria-label="Card front">
  <svg class="front-header" viewBox="0 0 400 420" aria-hidden="true">
    <polygon points="0,0 400,0 400,290 200,372 0,290" fill="var(--ink)"/>
    <polyline points="0,300 200,384 400,300" fill="none" stroke="var(--red)" stroke-width="7"/>
  </svg>
  <div class="brand-front">QUORVANEX</div>

  <div class="contact">
    <p class="contact-name">Lorraine K. Vestal</p>
    <p class="contact-title">CEO</p>
    <p class="contact-address">P.O. Box 47315<br>Fernhollow, Calder 00000</p>
    <ul class="contact-lines">
      <li>
        <svg viewBox="0 0 16 16" aria-hidden="true"><path d="M3 5a3 3 0 0 1 2-2l1.5 3-1.2 1a7 7 0 0 0 3.7 3.7l1-1.2 3 1.5a3 3 0 0 1-2 2C6.5 13 3 9.5 3 5z" fill="var(--red)"/></svg>
        555.417.3820
      </li>
      <li>
        <svg viewBox="0 0 16 16" aria-hidden="true"><rect x="1" y="3" width="14" height="10" fill="var(--red)"/><polyline points="1,3 8,9 15,3" fill="none" stroke="#fff" stroke-width="1.3"/></svg>
        LVestal@Quorvanexco.com
      </li>
      <li>
        <svg viewBox="0 0 16 16" aria-hidden="true"><circle cx="8" cy="8" r="7" fill="var(--red)"/><ellipse cx="8" cy="8" rx="3" ry="7" fill="none" stroke="#fff" stroke-width="1"/><line x1="1" y1="8" x2="15" y2="8" stroke="#fff" stroke-width="1"/></svg>
        www.quorvanexco.com
      </li>
    </ul>
  </div>
</section>

<section class="card card-back" aria-label="Card back">
  <div class="brand-back"><span class="mark" aria-hidden="true"></span>QUORVANEX</div>
  <p class="coupon-note">Sign up on our website for a coupon code</p>
</section>

</body>
</html>
```